Rebrand stationary with recently completed logo design

Need new business cards, thank you cards, letterhead, envelopes and presentation folders. The designs will be sent to a separate production firm so I need the files to be print ready.

My contact info
Reko Haliburn

Office 604-318-5047
Fax 604-371-8054

Email reko@glazemark.ca
website www.glazemark.ca

315-14720 62nd Avenue,
Langley, BC, V2K 3R8

Target Market(s)

Homeowners, businesses and contractors

Industry/Entity Type

Business

Font styles to use
Sans Serif

Colors
34a7d7

Requirements
Must have
• Like to have one side of the business card a solid color with the logo in all white. The side with all the text to be a white background
• I find the current blue on the front of the card with the white logo too dark.
Should not have
• Gradient colors

```html
<!DOCTYPE html>
<html lang="en">
<head>
<meta charset="utf-8">
<title>Glazemark Business Card</title>
<link href="https://fonts.googleapis.com/css2?family=Open+Sans:wght@400;600&family=PT+Sans+Narrow:wght@700&display=swap" rel="stylesheet">
<style>
  :root {
    --page: #e8e5e0;
    --card: #fbfbfb;
    --brand-blue: #34a7d7;
    --slate: #3f4f5b;
    --text: #4a4a4a;
    --rule: #c9c9c9;
  }
  html, body {
    margin: 0;
    padding: 0;
    width: 1200px;
    height: 960px;
    overflow: hidden;
    background: var(--page);
    font-family: "Open Sans", sans-serif;
  }
  .canvas { position: relative; width: 1200px; height: 960px; }

  .card {
    position: absolute;
    width: 600px;
    height: 342px;
    background: var(--card);
    box-shadow: 0 2px 6px rgba(0,0,0,0.25);
    overflow: hidden;
  }
  .card--front { left: 302px; top: 129px; }
  .card--back  { left: 299px; top: 489px; }

  .wordmark {
    position: absolute;
    font-family: "Open Sans", sans-serif;
    font-weight: 400;
    letter-spacing: 0.5px;
    white-space: nowrap;
  }
  .card--front .wordmark {
    left: 80px; top: 178px;
    font-size: 34px;
    color: var(--slate);
  }

  .divider {
    position: absolute;
    left: 319px; top: 96px;
    width: 1px; height: 135px;
    background: var(--rule);
  }

  .contact { position: absolute; left: 347px; top: 94px; color: var(--text); }
  .contact__name {
    font-family: "PT Sans Narrow", sans-serif;
    font-weight: 700;
    font-size: 21px;
    color: var(--brand-blue);
    margin: 0 0 6px;
  }
  .contact__address { font-size: 13px; line-height: 18px; margin: 0 0 6px; }
  .contact__list { list-style: none; margin: 0; padding: 0; font-size: 13px; }
  .contact__list li { display: flex; align-items: center; height: 19px; }
  .contact__list svg { width: 12px; height: 12px; margin-right: 9px; fill: var(--brand-blue); }

  .web-band {
    position: absolute;
    left: 0; top: 294px;
    width: 527px; height: 32px;
    background: var(--brand-blue);
    color: #fff;
    font-size: 13px;
    letter-spacing: 3.5px;
    line-height: 32px;
    text-align: center;
    padding-left: 20px;
    box-sizing: border-box;
  }
  .web-band__end {
    position: absolute;
    left: 527px; top: 294px;
    width: 73px; height: 32px;
    background: var(--slate);
  }

  .card__panel {
    position: absolute;
    left: 14px; top: 12px;
    width: 572px; height: 316px;
    background: var(--slate);
  }
  .card--back .wordmark {
    left: 0; right: 0; top: 130px;
    text-align: center;
    font-size: 46px;
    color: #fff;
  }
</style>
</head>
<body>
<main class="canvas">

  <section class="card card--front" aria-label="Business card front">
    <div class="wordmark">GLAZEMARK</div>
    <div class="divider"></div>
    <div class="contact">
      <p class="contact__name">Reko Haliburn</p>
      <p class="contact__address">315-14720 62nd Avenue<br>Langley, BC, V2K 3R8</p>
      <ul class="contact__list">
        <li>
          <svg viewBox="0 0 12 12" aria-label="Phone"><path d="M2.4 0.5l2 2.2-1 1.3c.7 1.6 2 2.9 3.6 3.6l1.3-1 2.2 2-1.3 2c-4.5-.3-8.3-4.1-8.6-8.6z"/></svg>
          604-318-5047
        </li>
        <li>
          <svg viewBox="0 0 12 12" aria-label="Fax"><rect x="3" y="0.5" width="6" height="3"/><rect x="0.5" y="4" width="11" height="5" rx="1"/><rect x="3" y="8" width="6" height="3.5"/></svg>
          604-371-8054
        </li>
        <li>
          <svg viewBox="0 0 12 12" aria-label="Email"><path d="M0.5 2.5h11v7h-11z M0.5 2.5l5.5 4 5.5-4"/></svg>
          reko@glazemark.ca
        </li>
      </ul>
    </div>
    <div class="web-band">www.glazemark.ca</div>
    <div class="web-band__end"></div>
  </section>

  <section class="card card--back" aria-label="Business card back">
    <div class="card__panel"></div>
    <div class="wordmark">GLAZEMARK</div>
  </section>

</main>
</body>
</html>
```